Postcard Design

We are an upscale, full service real estate boutique based in Mt. Pleasant, SC. We will be having a Grand Opening of our beautiful, new office complete with high end custom home architecture and design. I will attach photos for your review. I would like to come up with a medium postcard to be mailed to clientele of Mt. Pleasant. Home prices between $300,000 - $2.2 million. The customers can call our office for the Grand Opening Listing Promotion or stop by our grand opening. We will have drawings for door prizes that include services at Brisklane Day Spa, Tangy Pepperpot gift certificates, and they can register to win a cruise with a listing presentation. Our Grand Opening will be a couple of different dates, April 7, 2016 and April 21, 2016. I will want an order that lists the 7th and another order that will list the 21. The look should have a very "relaxing, beach" feel, but not Myrtle Beach...should reflect colors of the ocean, like you are on vacation. I will include logos and pics for your review. Thank you!

```html
<!DOCTYPE html>
<html lang="en">
<head>
<meta charset="utf-8">
<title>Palmcrest Real Estate – Grand Opening Postcard</title>
<link rel="stylesheet" href="https://fonts.googleapis.com/css2?family=Open+Sans:wght@700;800&family=Andika:wght@400;700&display=swap">
<style>
:root{
  --navy:#0f4a98;
  --ocean:#1aa6da;
  --sky:#0aa8d6;
  --cream:#fdf3e1;
  --red:#ee4123;
  --white:#ffffff;
  --ink:#1a4d94;
  --line:#c8c8c8;
  --stage:#2a2a2a;
}
*{margin:0;padding:0;box-sizing:border-box}
html,body{width:960px;height:1200px;overflow:hidden;background:var(--stage)}
.canvas{position:relative;width:960px;height:1200px}
.card{position:absolute;left:120px;width:720px;height:560px;overflow:hidden;background:var(--white)}
.card--front{top:30px}
.card--back{top:608px}
.layer{position:absolute;left:0;top:0}
.headline{position:absolute;font-family:"Open Sans",sans-serif;font-weight:800;color:var(--white);letter-spacing:.3px}
.dates{position:absolute;font-family:"Open Sans",sans-serif;font-weight:700;color:var(--white)}
.body-text{position:absolute;font-family:"Andika",sans-serif;color:var(--ink)}
.brand{position:absolute;border-radius:50%;background:var(--white);display:flex;align-items:center;justify-content:center;text-align:center}
.brand__name{font-family:"Open Sans",sans-serif;font-weight:700;color:var(--ocean);line-height:1.15}
.photo-round{position:absolute;border-radius:50%;border:4px solid var(--white);background:linear-gradient(#cfe3ea 0%,#b9c9d9 45%,#7d9a6b 80%,#c9c1a9 100%)}
.price-pill{position:absolute;left:156px;top:364px;width:248px;height:63px;background:var(--ocean);border-radius:0 32px 32px 32px;color:var(--white);font-family:"Andika",sans-serif;font-size:18px;line-height:26px;text-align:center;padding-top:6px}
.phone{position:absolute;font-family:"Open Sans",sans-serif;font-weight:800}
.url-pill{position:absolute;background:var(--navy);color:var(--white);border-radius:16px;font-family:"Andika",sans-serif;font-size:17px;text-align:center}
.stamp{position:absolute;left:624px;top:26px;width:69px;height:74px;border:1.5px solid var(--line)}
.address-line{position:absolute;left:418px;width:248px;height:0;border-top:2px solid var(--line)}
.contact-band{position:absolute;left:0;top:424px;width:349px;height:90px;background:var(--navy);text-align:center;color:var(--white)}
</style>
</head>
<body>
<div class="canvas">

  <!-- Front side -->
  <section class="card card--front">
    <svg class="layer" width="720" height="560" viewBox="0 0 720 560">
      <defs>
        <linearGradient id="beach" x1="0" y1="0" x2="0" y2="1">
          <stop offset="0" stop-color="#dfe9f2"/>
          <stop offset="0.35" stop-color="#b7cfe3"/>
          <stop offset="0.45" stop-color="#34b6c9"/>
          <stop offset="0.6" stop-color="#6fd0d6"/>
          <stop offset="0.72" stop-color="#f2f2ee"/>
          <stop offset="1" stop-color="#eae3d6"/>
        </linearGradient>
      </defs>
      <rect x="0" y="60" width="720" height="380" fill="url(#beach)" role="img" aria-label="Photo of a couple relaxing in striped beach chairs on a white sand beach by turquoise water"/>
      <path d="M0 0 H720 V190 C700 150 670 110 620 70 C540 30 440 40 330 90 C230 135 120 145 0 118 Z" fill="var(--ocean)"/>
      <path d="M0 0 H720 V40 C620 40 520 40 420 60 C320 80 230 120 130 118 C70 116 30 110 0 104 Z" fill="var(--navy)"/>
      <path d="M0 452 C140 460 260 420 380 402 C520 380 640 360 720 370 V560 H0 Z" fill="var(--cream)"/>
    </svg>

    <h1 class="headline" style="left:30px;top:22px;font-size:27px">GRAND OPENING ON</h1>
    <p class="dates" style="left:34px;top:58px;font-size:18px">April 7, 2016 &amp; April 21, 2016</p>

    <div class="brand" style="left:514px;top:18px;width:188px;height:188px">
      <span class="brand__name" style="font-size:22px">PALMCREST<br><span style="font-size:11px;letter-spacing:3px">REAL ESTATE</span></span>
    </div>

    <div class="photo-round" style="left:10px;top:308px;width:148px;height:148px" role="img" aria-label="Photo of a light blue two-storey coastal home among trees"></div>
    <div class="price-pill">Home prices between<br>$300,000 - $2.2 million.</div>

    <p class="body-text" style="left:22px;top:480px;font-size:18px">You can register to win</p>
    <p class="body-text" style="left:22px;top:507px;font-size:18px;font-weight:700">a cruise with a listing presentation</p>

    <p class="body-text" style="left:420px;top:398px;width:288px;text-align:center;font-size:20px;line-height:26px">Call us for Grand<br>Opening Promotion</p>
    <p class="phone" style="left:420px;top:456px;width:288px;text-align:center;font-size:32px;color:var(--red)">843-555-0172</p>
    <p class="url-pill" style="left:408px;top:502px;width:272px;height:32px;line-height:32px">www.palmcrestrealestate.com</p>
  </section>

  <!-- Back side -->
  <section class="card card--back">
    <svg class="layer" width="720" height="560" viewBox="0 0 720 560">
      <defs>
        <linearGradient id="home" x1="0" y1="0" x2="0" y2="1">
          <stop offset="0" stop-color="#c9dcef"/>
          <stop offset="0.45" stop-color="#a9bfd6"/>
          <stop offset="0.8" stop-color="#7c9360"/>
          <stop offset="1" stop-color="#a69c7c"/>
        </linearGradient>
      </defs>
      <rect x="0" y="0" width="349" height="260" fill="url(#home)" role="img" aria-label="Photo of a light blue two-storey coastal home with shuttered windows among tall trees"/>
      <path d="M0 205 C80 190 160 222 230 238 C290 250 330 225 349 180 V560 H0 Z" fill="var(--navy)"/>
      <path d="M0 222 C80 210 160 245 240 258 C300 266 335 240 349 205 V560 H0 Z" fill="var(--sky)"/>
    </svg>

    <div class="brand" style="left:20px;top:148px;width:144px;height:144px">
      <span class="brand__name" style="font-size:17px">PALMCREST<br><span style="font-size:9px;letter-spacing:2.5px">REAL ESTATE</span></span>
    </div>

    <h2 class="headline" style="left:0;top:296px;width:349px;text-align:center;font-size:26px">GRAND OPENING ON</h2>
    <p class="dates" style="left:0;top:334px;width:349px;text-align:center;font-size:18px">April 7, 2016 &amp; April 21, 2016</p>
    <p class="body-text" style="left:0;top:368px;width:349px;text-align:center;font-size:17px;line-height:22px">Call us for Grand Opening<br>Promotion &amp; Registration</p>

    <div class="contact-band">
      <p class="phone" style="left:0;top:12px;width:349px;font-size:32px;color:var(--white)">843-555-0172</p>
      <p class="body-text" style="left:0;top:56px;width:349px;font-size:18px;color:var(--white);font-weight:700">www.palmcrestrealestate.com</p>
    </div>

    <div class="stamp"></div>
    <div class="address-line" style="top:309px"></div>
    <div class="address-line" style="top:350px"></div>
    <div class="address-line" style="top:392px"></div>
    <div class="address-line" style="top:434px"></div>
  </section>

</div>
</body>
</html>
```